I would like a business card to match my truck wrap and logo. I would like the font to match my existing business card please.

Industry/Entity Type

Painter

Contact Information for Business Card

Rodrigo Fenwar 801-437-2190 Fenwarcoatings.utah@brelmox.com
SERVICES - Custom Paint & Stain, Interior & Exterior, Epoxy Coatings / Garage Floors, Cabinet Refinishing, Log Staining and Refinishing.

Requirements
Nice to have
• I would like to have the white and grey line like the bottom of my vehicle wrap, Light Grey to match my truck also.

```html
<!DOCTYPE html>
<html lang="en">
<head>
<meta charset="utf-8">
<title>Fenwar Coatings – Business Card</title>
<link rel="stylesheet" href="https://fonts.googleapis.com/css2?family=Arimo:wght@400&family=Russo+One&display=swap">
<style>
  :root {
    --bg: #262626;
    --white: #ffffff;
    --blue-light: #0aa9ea;
    --blue-mid: #0a8fd6;
    --blue-deep: #145a9c;
    --grey-line: #b9bcc4;
    --ink: #1b1b1b;
  }
  * { margin: 0; padding: 0; box-sizing: border-box; }
  html, body { width: 1200px; height: 1015px; overflow: hidden; background: var(--bg); }
  .canvas { position: relative; width: 1200px; height: 1015px; }

  .card {
    position: absolute; left: 210px; width: 780px; height: 446px;
    overflow: hidden; box-shadow: 0 10px 30px rgba(0,0,0,.55);
  }
  .card--back { top: 40px; background: linear-gradient(180deg, var(--blue-light) 0%, var(--blue-mid) 50%, var(--blue-deep) 100%); }
  .card--front { top: 529px; background: var(--white); }

  .pattern-area {
    position: absolute; inset: 0;
    background: linear-gradient(160deg, rgba(255,255,255,.08), rgba(0,0,0,.12));
  }
  .brand {
    position: absolute; display: flex; align-items: center; gap: 14px;
    font-family: "Russo One", sans-serif; line-height: 1;
  }
  .brand__mark { display: block; flex: none; }
  .brand__name { display: flex; flex-direction: column; gap: 6px; }
  .card--back .brand { left: 300px; top: 180px; color: var(--white); font-size: 52px; }
  .card--back .brand__mark { width: 76px; height: 76px; background: var(--white); }
  .brand__sub { font-size: 0.42em; letter-spacing: 0.62em; }

  .card--front .brand { left: 48px; top: 118px; color: var(--blue-light); font-size: 44px; }
  .card--front .brand__mark { width: 62px; height: 62px; background: var(--blue-light); }

  .divider { position: absolute; left: 0; top: 0; }
  .band { position: absolute; left: 0; top: 0; }

  .contact { position: absolute; left: 388px; top: 72px; }
  .contact__name {
    font-family: "Russo One", sans-serif; color: var(--blue-mid);
    font-size: 29px; letter-spacing: .5px; text-transform: uppercase; margin-bottom: 26px;
  }
  .contact__line {
    display: flex; align-items: center; gap: 10px;
    font-family: "Arimo", sans-serif; color: var(--ink); font-size: 19px; margin-bottom: 10px;
  }
  .contact__line svg { flex: none; }

  .services {
    position: absolute; list-style: none;
    font-family: "Arimo", sans-serif; color: var(--white); font-size: 21px; line-height: 1.5;
  }
  .services li::before { content: "●"; font-size: 13px; margin-right: 10px; vertical-align: 3px; }
  .services--left { left: 60px; top: 352px; }
  .services--right { left: 470px; top: 232px; }
</style>
</head>
<body>
<main class="canvas">

  <section class="card card--back" aria-label="Card back">
    <div class="pattern-area" role="img" aria-label="Repeating tonal pattern of painting-tool tiles across the blue background"></div>
    <div class="brand">
      <span class="brand__mark"></span>
      <span class="brand__name"><span>FENWAR</span><span class="brand__sub">COATINGS</span></span>
    </div>
  </section>

  <section class="card card--front" aria-label="Card front">
    <svg class="band" width="780" height="446" viewBox="0 0 780 446" aria-hidden="true">
      <defs>
        <linearGradient id="bandFill" x1="0" y1="0" x2="0" y2="1">
          <stop offset="0" stop-color="#0aa9ea"/>
          <stop offset="1" stop-color="#145a9c"/>
        </linearGradient>
      </defs>
      <path d="M0 334 L426 334 L452 214 L780 214 L780 446 L0 446 Z" fill="url(#bandFill)"/>
      <path d="M0 326 L420 326 L446 206 L780 206" fill="none" stroke="#b9bcc4" stroke-width="7"/>
    </svg>

    <svg class="divider" width="780" height="446" viewBox="0 0 780 446" aria-hidden="true">
      <line x1="352" y1="40" x2="372" y2="250" stroke="#cfd2d8" stroke-width="1.2"/>
    </svg>

    <div class="brand">
      <span class="brand__mark"></span>
      <span class="brand__name"><span>FENWAR</span><span class="brand__sub">COATINGS</span></span>
    </div>

    <div class="contact">
      <p class="contact__name">Rodrigo Fenwar</p>
      <p class="contact__line">
        <svg width="18" height="18" viewBox="0 0 24 24" aria-hidden="true"><path fill="#0a8fd6" d="M6.6 10.8a15.1 15.1 0 0 0 6.6 6.6l2.2-2.2a1 1 0 0 1 1-.25 11.4 11.4 0 0 0 3.6.57 1 1 0 0 1 1 1V20a1 1 0 0 1-1 1A17 17 0 0 1 3 4a1 1 0 0 1 1-1h3.5a1 1 0 0 1 1 1c0 1.25.2 2.45.57 3.6a1 1 0 0 1-.25 1z"/></svg>
        801-437-2190
      </p>
      <p class="contact__line">
        <svg width="20" height="14" viewBox="0 0 20 14" aria-hidden="true"><rect width="20" height="14" fill="#0a8fd6"/><path d="M0 0 L10 8 L20 0" fill="none" stroke="#fff" stroke-width="1.5"/></svg>
        Fenwarcoatings.utah@brelmox.com
      </p>
    </div>

    <ul class="services services--left">
      <li>Custom Paint &amp; Stain</li>
      <li>Interior &amp; Exterior</li>
    </ul>
    <ul class="services services--right">
      <li>Epoxy Coatings / Garage Floors</li>
      <li>Cabinet Refinishing</li>
      <li>Log Staining and Refinishing.</li>
    </ul>
  </section>

</main>
</body>
</html>
```